Computer consultant website

Plimvex Software is a newly started computer consulting company. It's a small one-man company that provides mostly Android applications but also websites in collaboration with designers. I'm running this company on the side of full time university studies.

I'm in need of a website which will function as:
Primarily - I'll direct potential clients to the page so they can read about the company, what i offer and past work.
Secondarily - Making my company visible through the web and maybe getting new clients.

The final design should look modern, clean and professional.

Pages that will be in the final website are (Note that it's not the exact titles as the page will not be in english):
* About
* Services (what Plimvex offers)
* Portfolio/work
* Short news (like ArtHivers "News and press")
* Contact.

Inspiration
http://www.arthiver.example/design/87836
http://www.brookwellstudio.example/
http://www.arthiver.example/design/845881
http://www.arthiver.example/design/1369424 - Lighter design, however a bit cluttered.

No programming code is needed delivered at all. Focus on designing rather then coding.

If you have any questions, do not hesitate to send me a message.

Target Market(s)

Non-technical entrepreneurs and small companies.

Industry/Entity Type

University

Requirements
Must have
• Must have my company logo (see attachment).

Must in any way use both colors from my logo.

A way to logically rearrange content to fit smaller screens. I will implement this design so that it can be pleasantly viewed on mobile devices. You don't necessarily need to provide exactly how the design would look on mobile devices.

I need the following types of page designs:
* Landing page
* Content page
* Portfolio/work (with accompanying inside/clicked) page

Landing/start page must in any way include at least the information:
* Shorter version of "About Plimvex"
* At least 1 most recent portfolio/work entry
* At least 1 most recent news entry
* Services that Plimvex offers.
Nice to have
• -
Should not have
• Testimonials or newsletter.

```html
<!DOCTYPE html>
<html lang="en">
<head>
<meta charset="utf-8">
<title>Plimvex Software – Works</title>
<link href="https://fonts.googleapis.com/css2?family=Open+Sans:wght@300;400;600;700&family=Tinos&display=swap" rel="stylesheet">
<style>
:root{
  --nav-bg:#363232;
  --accent:#2a7cf2;
  --ink:#333333;
  --muted:#666666;
  --page-bg:#f4f4f4;
  --white:#ffffff;
  --rule:#d9d9d9;
  --footer-bg:#2e2e2e;
  --footer-text:#cfcfcf;
  --button-top:#e8e8e8;
  --button-bottom:#c4c4c4;
}
*{margin:0;padding:0;box-sizing:border-box}
html,body{width:1200px;height:1051px;overflow:hidden}
body{position:relative;background:var(--page-bg);font-family:'Open Sans',sans-serif;color:var(--ink)}
.abs{position:absolute}

.top-nav{left:0;top:0;width:1200px;height:52px;background:var(--nav-bg)}
.top-nav a{position:absolute;top:0;height:52px;line-height:52px;color:var(--white);text-decoration:none;font-size:16px}
.top-nav a.current{background:var(--accent);text-align:center}

.site-header{left:0;top:52px;width:1200px;height:116px;background:var(--white);border-bottom:1px solid #e6e6e6}
.brand{left:173px;top:31px;display:flex;align-items:center;gap:14px}
.brand-dot{width:56px;height:56px;border-radius:50%;background:var(--accent)}
.brand-name{font-size:46px;font-weight:600;color:var(--ink);letter-spacing:-1px}
.consult{right:179px;top:36px;display:flex;align-items:center;gap:7px}
.phone-icon{flex:none;display:block}
.consult-text{text-align:right;white-space:nowrap}
.consult-title{font-size:20px;color:var(--accent);line-height:23px}
.consult-phone{font-family:'Tinos',serif;font-size:27px;color:#555;line-height:27px;letter-spacing:1px}

.page-title{left:181px;top:192px;font-size:34px;font-weight:300;color:var(--ink)}
.title-rule{left:182px;top:240px;width:834px;height:1px;background:var(--rule)}
.filters{left:185px;top:259px;font-size:13px;color:#777}
.filters span{margin-right:6px}
.filters .sep{color:#bbb;margin:0 8px 0 2px}
.filters .on{color:var(--accent)}

.shot-frame{left:183px;top:298px;width:550px;height:407px;background:var(--white);border:1px solid #dcdcdc;box-shadow:0 1px 3px rgba(0,0,0,.08)}
.shot{left:191px;top:306px;width:533px;height:391px;background:linear-gradient(180deg,#2bb8e6 0%,#4fc6ea 38%,#bfe9f3 55%,#7eb83a 100%)}

.project{left:756px;top:296px;width:258px}
.project-name{font-size:12.5px;color:var(--accent);line-height:18px}
.project-type{font-size:12.5px;color:#555;line-height:18px;margin-top:3px}
.project-rule{border-top:1px dashed #c9c9c9;margin:9px 2px 0 0}
.project-head{font-size:12.5px;font-weight:600;color:#444;margin-top:14px}
.project p{font-size:12.3px;line-height:17.1px;color:#666;margin-top:3px}
.project p+p{margin-top:17px}

.btn{display:flex;align-items:center;justify-content:center;font-weight:700;color:#444;background:linear-gradient(180deg,var(--button-top),var(--button-bottom));border:1px solid #b5b5b5}
.visit{left:757px;top:660px;width:157px;height:45px;font-size:15.5px}

.cta{left:183px;top:749px;width:829px;height:111px;background:linear-gradient(180deg,#d6e8ff 0%,#9ec8ff 50%,#5e9ef5 100%);border:2px solid var(--white);box-shadow:0 0 2px rgba(0,0,0,.2)}
.cta-lead{right:470px;top:766px;font-size:34px;font-weight:300;color:var(--accent);text-align:right;line-height:40px}
.cta-sub{right:474px;top:800px;font-size:26px;color:var(--ink);line-height:32px}
.contact-btn{left:771px;top:777px;width:183px;height:53px;font-size:21px}

.site-footer{left:0;top:916px;width:1200px;height:135px;background:var(--footer-bg)}
.foot-links a{position:absolute;top:958px;font-size:12.5px;color:var(--white);text-decoration:none}
.copyright{left:188px;top:989px;font-size:12.5px;color:#aaa}
.touch{left:790px;top:942px;width:180px;text-align:center;font-size:12px;color:var(--white)}
.touch:before,.touch:after{content:"";position:absolute;top:8px;width:38px;height:1px;background:#555}
.touch:before{left:0}.touch:after{right:0}
.social{position:absolute;top:966px;width:34px;height:34px;border-radius:50%;background:#8a8a8a}
.call{left:780px;top:1014px;width:200px;text-align:center;font-size:12.5px;color:#6fa8ff}
</style>
</head>
<body>

<nav class="top-nav abs">
  <a style="left:189px">Home</a>
  <a style="left:265px">About</a>
  <a style="left:345px">Services</a>
  <a class="current" style="left:421px;width:74px">Works</a>
  <a style="left:512px">News</a>
  <a style="left:585px">Contact</a>
</nav>

<header class="site-header abs">
  <div class="brand abs"><span class="brand-dot"></span><span class="brand-name">Plimvex</span></div>
  <div class="consult abs">
    <svg class="phone-icon" width="18" height="40" viewBox="0 0 18 40" aria-hidden="true">
      <rect x="1" y="1" width="16" height="38" rx="2" fill="none" stroke="#666" stroke-width="2"/>
      <rect x="4" y="5" width="10" height="12" fill="#666"/>
      <g fill="#666"><rect x="4" y="21" width="3" height="3"/><rect x="8" y="21" width="3" height="3"/><rect x="12" y="21" width="3" height="3"/><rect x="4" y="26" width="3" height="3"/><rect x="8" y="26" width="3" height="3"/><rect x="12" y="26" width="3" height="3"/><rect x="4" y="31" width="3" height="3"/><rect x="8" y="31" width="3" height="3"/><rect x="12" y="31" width="3" height="3"/></g>
    </svg>
    <div class="consult-text">
      <div class="consult-title">Free Consultancy</div>
      <div class="consult-phone">013 579 2468</div>
    </div>
  </div>
</header>

<h1 class="page-title abs">Works</h1>
<div class="title-rule abs"></div>
<div class="filters abs">
  <span class="on">All</span><span class="sep">|</span><span>Android App</span><span class="sep">|</span><span>Website Design</span><span class="sep">|</span><span>SEO</span><span class="sep">|</span><span>User Experience Design</span>
</div>

<div class="shot-frame abs"></div>
<div class="shot abs" role="img" aria-label="Screenshot of the Meadow Dash game website: sky with clouds, green hills and the player sign-up panel"></div>

<section class="project abs">
  <div class="project-name">Meadow Dash</div>
  <div class="project-type">Website Design and Development</div>
  <div class="project-rule"></div>
  <div class="project-head">Project Description</div>
  <p>Sed eget placerat diam. In hac habitasse platea dictumst. Aliquam non rutrum eros. Suspendisse eu eros quis est mattis sodales in at enim. Aliquam sollicitudin, velit vel luctus feugiat, mi metus vestibulum diam, id interdum arcu arcu eu tortor.</p>
  <p>Quisque sodales dolor nec justo cursus a rhoncus felis scelerisque. Aliquam consectetur, massa in cursus vulputate, mauris sapien rutrum magna, quis euismod eros lacus nec felis. Maecenas pharetra arcu id tortor laoreet a ultricies justo rhoncus. Etiam et adipiscing tellus. Ut metus enim, adipiscing id feugiat et, commodo sed leo.</p>
</section>
<div class="btn visit abs">VISIT WEBSITE</div>

<div class="cta abs"></div>
<div class="cta-lead abs">Let's Discuss Your Project with us</div>
<div class="cta-sub abs">What do you need?</div>
<div class="btn contact-btn abs">CONTACT US</div>

<footer class="site-footer abs"></footer>
<div class="foot-links">
  <a style="left:188px">Home</a>
  <a style="left:247px">About</a>
  <a style="left:308px">Services</a>
  <a style="left:379px">Works</a>
  <a style="left:439px">News</a>
  <a style="left:495px">Contact</a>
</div>
<div class="copyright abs">Copyright © 2013 Plimvex. All rights reserved | Terms and Conditions | Privacy Policy</div>
<div class="touch abs">KEEP IN TOUCH</div>
<span class="social" style="left:780px"></span>
<span class="social" style="left:819px"></span>
<span class="social" style="left:859px"></span>
<span class="social" style="left:898px"></span>
<span class="social" style="left:939px"></span>
<div class="call abs">Call us at&nbsp; 013 579 2468</div>

</body>
</html>
```